Business Cards Design for the electrical wholesaler: clean bold dynamic :)

We need a business card design that would follow our latest brand guidelines. As an electrical wholesaler we want to bring a fresh look and feel into the industry. The design should be clean bold and dynamic. It should come alive with the renewed energy of our green colour. Our grey colour should keep things balanced and complement the notion of maturity and responsibility. We employ Lato as a corporate font however are not bound by this font and we’re open to interpretation here.

Target Market(s)

Electrical contractors

Industry/Entity Type

Business

Contact Information for Business Card

Logo
Name & Surname: Halyna Dorosh
Job Title: Director of Marketing
Email: halya.dorosh@quillmail.example
Cell phone: XXX.XXX.XXXX
Address: 20517 - 87 Ave. Edmonton, AB, Canada. T6K 4N8
Business Phone: 780.555.0184
Website: www.brovix.example

Font styles to use
Other font styles liked:
• Lato

Requirements
Must have
• Logo & website
Nice to have
• Brand elements - some of them you may find in the attached Brand Guidelines (e.g. three lines on the background signifying "W")

```html
<!DOCTYPE html>
<html lang="en">
<head>
<meta charset="utf-8">
<title>Brovix Business Card</title>
<link href="https://fonts.googleapis.com/css2?family=Lato:wght@400;700&display=swap" rel="stylesheet">
<style>
  :root {
    --backdrop: #3a3a3c;
    --card: #2a2a2c;
    --brand-green: #7dc21e;
    --brand-grey: #a9a9a9;
    --text-light: #f2f2f2;
  }
  * { margin: 0; padding: 0; box-sizing: border-box; }
  html, body {
    width: 799px; height: 1200px; overflow: hidden;
    background: var(--backdrop);
    font-family: "Lato", Arial, sans-serif;
  }
  .canvas {
    position: relative; width: 799px; height: 1200px;
  }
  .card {
    position: absolute; left: 90px;
    width: 620px; height: 354px;
    background: var(--card);
    border-radius: 22px;
    overflow: hidden;
    box-shadow: 0 14px 30px rgba(0,0,0,.45);
  }
  .card--front { top: 130px; }
  .card--back { top: 716px; }

  .wordmark {
    display: flex; align-items: center; gap: 12px;
    font-weight: 700; color: var(--brand-grey);
    line-height: 1;
  }
  .wordmark__dot {
    background: var(--brand-green);
    border-radius: 50%;
  }
  .card--front .wordmark {
    position: absolute; left: 50%; top: 50%;
    transform: translate(-50%, -50%);
    font-size: 88px;
  }
  .card--front .wordmark__dot { width: 36px; height: 36px; }

  .card--back .wordmark {
    position: absolute; left: 30px; top: 26px;
    font-size: 42px; gap: 8px;
  }
  .card--back .wordmark__dot { width: 18px; height: 18px; }

  .accent-bands {
    position: absolute; right: 0; top: 0;
    width: 260px; height: 354px;
  }

  .contact {
    position: absolute; left: 30px; top: 104px;
    color: var(--text-light);
  }
  .contact__name {
    font-size: 27px; font-weight: 700;
    color: var(--brand-green);
  }
  .contact__role { font-size: 16px; margin-top: 2px; }
  .contact__address { font-size: 15px; line-height: 1.35; margin-top: 14px; }
  .contact__lines { list-style: none; margin-top: 14px; }
  .contact__lines li {
    display: flex; align-items: center; gap: 9px;
    font-size: 15px; line-height: 1.55;
  }
  .contact__icon { width: 14px; height: 14px; flex: none; }
</style>
</head>
<body>
<main class="canvas">

  <section class="card card--front" aria-label="Card front">
    <div class="wordmark"><span class="wordmark__dot"></span><span>brovix</span></div>
  </section>

  <section class="card card--back" aria-label="Card back">
    <svg class="accent-bands" viewBox="0 0 260 354" aria-hidden="true">
      <path d="M150 0 H260 V354 H170 C215 250 215 100 150 0 Z" fill="var(--brand-grey)"/>
      <path d="M200 0 H260 V354 H215 C255 250 255 100 200 0 Z" fill="var(--brand-green)"/>
    </svg>

    <div class="wordmark"><span class="wordmark__dot"></span><span>brovix</span></div>

    <div class="contact">
      <p class="contact__name">Halyna Dorosh</p>
      <p class="contact__role">Founder &amp; CEO</p>
      <p class="contact__address">20517 - 87 Ave. Edmonton,<br>AB, Canada T6K 4N8</p>
      <ul class="contact__lines">
        <li>
          <svg class="contact__icon" viewBox="0 0 14 14" aria-hidden="true"><circle cx="7" cy="7" r="7" fill="var(--brand-green)"/><path d="M4.3 3.6c.4-.3.8-.2 1 .2l.6 1.1c.2.3.1.6-.2.8l-.4.3c.4.9 1.1 1.6 2 2l.3-.4c.2-.3.5-.4.8-.2l1.1.6c.4.2.5.6.2 1-.6.9-1.5 1-2.5.5C5.6 9 4.9 8.3 4.3 7 3.8 5.9 3.6 4.3 4.3 3.6z" fill="#2a2a2c"/></svg>
          <span>+1 780-555-0184</span>
        </li>
        <li>
          <svg class="contact__icon" viewBox="0 0 14 14" aria-hidden="true"><circle cx="7" cy="7" r="7" fill="var(--brand-green)"/><rect x="3.5" y="4.5" width="7" height="5" fill="none" stroke="#2a2a2c" stroke-width="1"/><path d="M3.5 4.5 7 7.3 10.5 4.5" fill="none" stroke="#2a2a2c" stroke-width="1"/></svg>
          <span>halya.dorosh@quillmail.example</span>
        </li>
        <li>
          <svg class="contact__icon" viewBox="0 0 14 14" aria-hidden="true"><circle cx="7" cy="7" r="7" fill="var(--brand-green)"/><circle cx="7" cy="7" r="3.6" fill="none" stroke="#2a2a2c" stroke-width="1"/><ellipse cx="7" cy="7" rx="1.5" ry="3.6" fill="none" stroke="#2a2a2c" stroke-width="1"/><path d="M3.4 7h7.2" stroke="#2a2a2c" stroke-width="1"/></svg>
          <span>www.brovix.example</span>
        </li>
      </ul>
    </div>
  </section>

</main>
</body>
</html>
```